KESTREL Academy Exhibit Booth Posters

My company is KESTREL Academy (a division of KESTREL for Growth). We are exhibiting in a month, and I need to re-do my exhibit booth posters. There will be a total of 4 posters needed. Sizes are below.
1) Top- 11 feet long X 12 inches wide (Try to match color scheme in example photo)
2) Center- 4 feet long X 2 feet wide (Chalkboard background)
3) Left- 18 inches long X 2 feet wide (Cork-board back ground with the use of push pins holding up post-it-notes, paper, etc.)
4) Right- 18 inches long X 2 feet wide (Cork-board back ground with the use of push pins holding up post-it-notes, paper, etc.)
I have attached a photo of my old booth. This will get you an idea of the size, color schemes, and more. I have created basic rendering of each poster. The content is important, but the look and design should be drastically improved.
The websites to look into for ideas are:
www.kestrelforgrowth.example
www.kestrelacademy.example
Updates
I've added a new file. It's a .JPG of the certification diploma. Thanks!
Target Market(s)
Business Owners, Managers, HR, Supervisors, Teens who want to boost their resume
Industry/Entity Type
It Company
Look and feel

```html
<!DOCTYPE html>
<html lang="en">
<head>
<meta charset="utf-8">
<title>KESTREL Academy — Booth Poster</title>
<link href="https://fonts.googleapis.com/css2?family=Kalam:wght@400;700&family=Permanent+Marker&display=swap" rel="stylesheet">
<style>
  :root {
    --cork-light: #d6a66c;
    --cork-mid: #c8935a;
    --cork-dark: #b57d45;
    --legal-pad: #f7efb0;
    --legal-line: #9fb9cf;
    --margin-red: #d98a8a;
    --sheet-white: #f6f6f2;
    --sheet-line: #a9bfd6;
    --sticky-yellow: #f5e66a;
    --sticky-edge: #e9d64c;
    --ink: #1c1c1c;
    --sticky-ink: #a4261c;
    --pin-red: #d3231f;
    --pin-dark: #8d1210;
    --bullet-red: #d8261f;
  }
  * { box-sizing: border-box; margin: 0; padding: 0; }
  html, body { width: 900px; height: 1200px; overflow: hidden; }
  body { background: var(--cork-mid); }

  .poster {
    position: relative;
    width: 900px;
    height: 1200px;
    overflow: hidden;
  }
  .cork-board {
    position: absolute; inset: 0;
    background: radial-gradient(ellipse at 50% 40%, var(--cork-light), var(--cork-mid) 60%, var(--cork-dark));
  }

  .note {
    position: absolute;
    box-shadow: 4px 8px 14px rgba(60, 30, 5, 0.35);
  }

  /* Headline sheet */
  .headline-sheet {
    left: 58px; top: 40px; width: 780px; height: 330px;
    transform: rotate(-2.4deg);
    background:
      radial-gradient(circle at 50% 50%, var(--cork-mid) 11px, transparent 12px) 8px 10px / 32px 32px repeat-x,
      linear-gradient(90deg, transparent 112px, var(--margin-red) 112px, var(--margin-red) 114px, transparent 114px),
      repeating-linear-gradient(180deg, transparent 0 44px, var(--legal-line) 44px 45px) 0 30px / 100% 100% no-repeat,
      var(--legal-pad);
    clip-path: polygon(0 0, 100% 0, 100% 82%, 96% 86%, 91% 83%, 84% 88%, 77% 84%, 70% 90%, 62% 86%, 54% 91%, 46% 87%, 38% 93%, 30% 89%, 22% 95%, 14% 92%, 7% 97%, 0 94%);
  }
  .headline {
    position: absolute; left: 90px; top: 110px; width: 640px;
    font-family: 'Kalam', cursive;
    font-weight: 700;
    font-size: 64px;
    line-height: 88px;
    color: var(--ink);
    transform: rotate(-1deg);
  }

  /* Lined sheet with topics */
  .topics-sheet {
    left: 62px; top: 378px; width: 790px; height: 440px;
    transform: rotate(2.6deg);
    background:
      radial-gradient(circle at 50% 50%, var(--cork-mid) 12px, transparent 13px) 24px 6px / 36px 36px repeat-x,
      linear-gradient(90deg, transparent 102px, var(--margin-red) 102px, var(--margin-red) 104px, transparent 104px),
      repeating-linear-gradient(180deg, transparent 0 30px, var(--sheet-line) 30px 31px) 0 40px / 100% 100% no-repeat,
      var(--sheet-white);
    clip-path: polygon(0 0, 100% 0, 100% 92%, 94% 95%, 86% 92%, 78% 96%, 70% 93%, 60% 98%, 50% 94%, 40% 99%, 30% 95%, 20% 100%, 10% 96%, 0 99%);
  }
  .topic-list {
    position: absolute; left: 78px; top: 70px;
    list-style: none;
    font-family: 'Kalam', cursive;
    font-size: 44px;
    line-height: 88px;
    color: var(--ink);
  }
  .topic-list li { position: relative; padding-left: 58px; }
  .topic-list li::before {
    content: ""; position: absolute; left: 0; top: 36px;
    width: 14px; height: 14px; border-radius: 50%;
    background: var(--bullet-red);
  }

  /* Sticky notes */
  .sticky {
    background: linear-gradient(160deg, var(--sticky-yellow), var(--sticky-edge));
    font-family: 'Permanent Marker', cursive;
    color: var(--sticky-ink);
  }
  .sticky-habits {
    left: 40px; top: 798px; width: 400px; height: 360px;
    transform: rotate(-4deg);
  }
  .habits-text {
    position: absolute; left: 40px; top: 110px;
    font-size: 38px; line-height: 56px;
    transform: rotate(-20deg);
    list-style: none;
  }
  .habits-text li.item { padding-left: 20px; }
  .sticky-peek {
    left: 476px; top: 762px; width: 392px; height: 362px;
    transform: rotate(7deg);
  }
  .peek-text {
    position: absolute; left: 60px; top: 55px;
    font-size: 44px; line-height: 64px;
    text-align: center;
    transform: rotate(20deg);
  }

  /* Push pins */
  .pin { position: absolute; width: 44px; height: 48px; z-index: 5; }
</style>
</head>
<body>
<main class="poster">
  <div class="cork-board" role="img" aria-label="Cork board background texture"></div>

  <section class="note headline-sheet">
    <h1 class="headline">Content Based On Employer Feedback</h1>
  </section>

  <section class="note topics-sheet">
    <ul class="topic-list">
      <li>Its More Than a Paycheck</li>
      <li>Its All About Attitude</li>
      <li>Play by The Rules</li>
      <li>And Much more</li>
    </ul>
  </section>

  <aside class="note sticky sticky-habits">
    <ul class="habits-text">
      <li>Be..</li>
      <li class="item">• There</li>
      <li class="item">• On Time</li>
      <li class="item">• Focused</li>
    </ul>
  </aside>

  <aside class="note sticky sticky-peek">
    <p class="peek-text">Ask Us<br>About A<br>Sneak Peek</p>
  </aside>

  <svg class="pin" style="left:96px; top:100px" viewBox="0 0 44 48" aria-hidden="true">
    <circle cx="22" cy="20" r="16" fill="var(--pin-red)"/><circle cx="17" cy="14" r="5" fill="#f28b86"/><circle cx="22" cy="20" r="16" fill="none" stroke="var(--pin-dark)" stroke-width="2"/>
  </svg>
  <svg class="pin" style="left:784px; top:50px" viewBox="0 0 44 48" aria-hidden="true">
    <circle cx="22" cy="20" r="16" fill="var(--pin-red)"/><circle cx="17" cy="14" r="5" fill="#f28b86"/><circle cx="22" cy="20" r="16" fill="none" stroke="var(--pin-dark)" stroke-width="2"/>
  </svg>
  <svg class="pin" style="left:152px; top:370px" viewBox="0 0 44 48" aria-hidden="true">
    <circle cx="22" cy="20" r="16" fill="var(--pin-red)"/><circle cx="17" cy="14" r="5" fill="#f28b86"/><circle cx="22" cy="20" r="16" fill="none" stroke="var(--pin-dark)" stroke-width="2"/>
  </svg>
  <svg class="pin" style="left:792px; top:586px" viewBox="0 0 44 48" aria-hidden="true">
    <circle cx="22" cy="20" r="16" fill="var(--pin-red)"/><circle cx="17" cy="14" r="5" fill="#f28b86"/><circle cx="22" cy="20" r="16" fill="none" stroke="var(--pin-dark)" stroke-width="2"/>
  </svg>
  <svg class="pin" style="left:166px; top:818px" viewBox="0 0 44 48" aria-hidden="true">
    <circle cx="22" cy="20" r="16" fill="var(--pin-red)"/><circle cx="17" cy="14" r="5" fill="#f28b86"/><circle cx="22" cy="20" r="16" fill="none" stroke="var(--pin-dark)" stroke-width="2"/>
  </svg>
  <svg class="pin" style="left:694px; top:784px" viewBox="0 0 44 48" aria-hidden="true">
    <circle cx="22" cy="20" r="16" fill="var(--pin-red)"/><circle cx="17" cy="14" r="5" fill="#f28b86"/><circle cx="22" cy="20" r="16" fill="none" stroke="var(--pin-dark)" stroke-width="2"/>
  </svg>
</main>
</body>
</html>
```